Brightfield Ventures Inc. Letterhead

Creation of attractive and eye catching letterhead for a business start-up for the construction industry. Letterhead must relate to construction, but avoid standard hammer and tools in the design.

I forgot to add some details, sorry about that. Some pertinent info: Ph: 916-555-0187 brightfieldventures.example 448 Willowmere Ave, Ste 210 Folsom, CA 95999 info@brightfieldventures.example not sure if slogan should be in there" “Connecting construction professionals to create a purpose driven industry.” must be able to be used in word. Thanks!

```html
<!DOCTYPE html>
<html lang="en">
<head>
<meta charset="utf-8">
<title>Brightfield Ventures Inc. Letterhead</title>
<link href="https://fonts.googleapis.com/css2?family=Arimo:wght@400;700&display=swap" rel="stylesheet">
<style>
:root{
  --backdrop:#b7d1e6;
  --paper:#ffffff;
  --navy:#1f2a6b;
  --red:#c8202a;
  --ink:#1c1c1c;
  --muted:#6d6d6d;
  --sign-tone:#e4e4e4;
}
*{box-sizing:border-box;margin:0;padding:0}
html,body{width:1200px;height:784px;overflow:hidden}
body{background:var(--backdrop);font-family:"Arimo",Arial,sans-serif;position:relative}
.letterhead{
  position:absolute;left:335px;top:17px;width:530px;height:750px;
  background:var(--paper);box-shadow:0 4px 14px rgba(40,70,110,.25);overflow:hidden;
}
.accent-red{position:absolute;left:52px;top:0;width:9px;height:30px;background:var(--red)}
.side-band{position:absolute;left:34px;top:62px;width:8px;height:688px;background:var(--navy)}
.brand{position:absolute;left:56px;top:40px;display:flex;align-items:center;gap:7px}
.brand-mark{width:10px;height:10px;background:var(--navy)}
.brand-name{font-size:14px;font-weight:700;color:var(--navy);letter-spacing:.3px}
.contact{position:absolute;right:34px;top:40px;text-align:right;font-size:8px;line-height:12px;color:var(--muted)}
.contact .company{font-size:10.5px;font-weight:700;color:var(--red);margin-bottom:3px}
.contact li{list-style:none;display:flex;justify-content:flex-end;align-items:center;gap:5px}
.contact li::after{content:"";width:5px;height:5px;border-radius:50%;background:var(--red)}
.letter-body{position:absolute;left:76px;top:150px;width:378px;font-size:9.4px;line-height:13.2px;color:var(--ink)}
.letter-body p{margin-bottom:13px;text-indent:14px}
.signature{position:absolute;left:80px;top:530px;width:140px;height:40px;background:var(--sign-tone);border-radius:3px}
</style>
</head>
<body>
<article class="letterhead">
  <div class="accent-red"></div>
  <div class="side-band"></div>
  <div class="brand"><span class="brand-mark"></span><span class="brand-name">Brightfield Ventures</span></div>
  <address class="contact">
    <div class="company">Brightfield Ventures Inc.</div>
    <ul>
      <li>448 Willowmere Ave, Ste 210</li>
      <li>Folsom, CA 95999</li>
      <li>Ph: 916-555-0187</li>
      <li>Fax: 916-555-0142</li>
      <li>info@brightfieldventures.example</li>
      <li>www.brightfieldventures.example</li>
    </ul>
  </address>
  <section class="letter-body">
    <p>Lorem Ipsum is simply dummy text of the printing and typesetting industry. Lorem Ipsum has been the industry's standard dummy text ever since the 1500s, when an unknown printer took a galley of type and scrambled it to make a type specimen book. It has survived not only five centuries, but also the leap into electronic typesetting, remaining essentially unchanged. It was popularised in the 1960s with the release of Typeline sheets containing Lorem Ipsum passages, and more recently with desktop publishing software like Folio PageSetter including versions of Lorem Ipsum.</p>
    <p>It is a long established fact that a reader will be distracted by the readable content of a page when looking at its layout. The point of using Lorem Ipsum is that it has a more-or-less normal distribution of letters, as opposed to using 'Content here, content here', making it look like readable English. Many desktop publishing packages and web page editors now use Lorem Ipsum as their default model text, and a search for 'lorem ipsum' will uncover many web sites still in their infancy. Various versions have evolved over the years, sometimes by accident, sometimes on purpose (injected humour and the like).</p>
    <p>Contrary to popular belief, Lorem Ipsum is not simply random text. It has roots in a piece of classical Latin literature from 45 BC, making it over 2000 years old. Richard Hollowell, a Latin professor at Larchmont College in Virginia, looked up one of the more obscure Latin words, consectetur, from a Lorem Ipsum passage, and going through the cites of the word in classical literature, discovered the undoubtable source. Lorem Ipsum comes from sections 1.10.32 and 1.10.33 of "de Finibus Bonorum et Malorum" structures, to generate Lorem Ipsum which looks reasonable. The generated Lorem Ipsum is therefore always free from repetition, injected humour, or non-characteristic words etc.</p>
  </section>
  <div class="signature" role="img" aria-label="Handwritten signature of the sender"></div>
</article>
</body>
</html>
```